Business card design for holistic health care clinic

We need a double-sided business card design for our holistic health care clinic that integrates our logo design and also its color scheme. My business is called Valmira. It is an integrative medicine clinic. You have already done the logo for me. Please ensure an elegant and upscale design that is not cluttered, but still has all the necessary information (please see below for details).

Target Market(s)

Wellness, fitness, rehabilitation for educated, well-traveled open-minded clients who are focused on natural, organic, balanced and preventive healthcare and lifestyle.

Industry/Entity Type

Medical

Contact Information for Business Card

Modern, clean.

Number of Pages Required

1 page

Font styles to use
Serif
Sans Serif

Colors

Designer to choose colors to be used in the design.

Requirements
Must have
• Logo on one side, all other information on the other side.
• Other information should include:
• Tobias Wrenfeld - DOE, CPT, LMT
• 4100 East Marrow Drive
• Austin, TX 78119
• 512 555 0148
• 818 555 0192
• info@ValmiraHealth.example
• t.wrenfeld@ValmiraHealth.example
Nice to have
• Darker background on front - but not totally black - shaded/dark gray.

```html
<!DOCTYPE html>
<html lang="en">
<head>
<meta charset="utf-8">
<title>Valmira Business Card</title>
<link rel="stylesheet" href="https://fonts.googleapis.com/css2?family=Montserrat:wght@600;700&family=Oswald:wght@500&family=Work+Sans:wght@400&display=swap">
<style>
  :root {
    --backdrop: #1b1b1b;
    --card: #262626;
    --card-edge: #2e2e2e;
    --accent: #1a9ad6;
    --ink: #f2f2f2;
  }
  * { margin: 0; padding: 0; box-sizing: border-box; }
  html, body { width: 1200px; height: 900px; overflow: hidden; background: var(--backdrop); }
  .canvas {
    position: relative; width: 1200px; height: 900px;
    background: radial-gradient(ellipse at 60% 40%, #2a2a2a 0%, var(--backdrop) 70%);
  }
  .card {
    position: absolute; left: 270px; width: 660px; height: 378px;
    background: linear-gradient(135deg, var(--card) 0%, var(--card-edge) 100%);
    box-shadow: 0 14px 30px rgba(0,0,0,0.55);
    overflow: hidden;
  }
  .card--front { top: 50px; }
  .card--back { top: 472px; }
  .card__stripe {
    position: absolute; left: 0; right: 0; bottom: 0; height: 7px; background: var(--accent);
  }
  /* Front */
  .brand {
    position: absolute; left: 0; right: 0; top: 112px; text-align: center;
  }
  .brand__name {
    font-family: "Montserrat", sans-serif; font-weight: 700;
    font-size: 88px; letter-spacing: 2px; color: var(--accent); line-height: 1;
    text-transform: uppercase;
  }
  .brand__tagline {
    margin-top: 10px;
    font-family: "Montserrat", sans-serif; font-weight: 600;
    font-size: 24px; letter-spacing: 1px; color: var(--accent);
  }
  .website {
    position: absolute; left: 0; right: 0; bottom: 28px; text-align: center;
    font-family: "Work Sans", sans-serif; font-size: 16px; letter-spacing: 2px; color: var(--ink);
  }
  .website__domain { color: var(--accent); }
  /* Back */
  .identity {
    position: absolute; right: 390px; top: 150px; text-align: right;
  }
  .identity__name {
    font-family: "Oswald", sans-serif; font-weight: 500; font-size: 44px;
    color: var(--accent); text-transform: uppercase; line-height: 1; letter-spacing: 1px;
  }
  .identity__credentials {
    margin-top: 10px;
    font-family: "Work Sans", sans-serif; font-size: 18px; color: var(--ink); letter-spacing: 1px;
  }
  .divider {
    position: absolute; left: 290px; top: 146px; width: 2px; height: 92px; background: var(--accent);
  }
  .contacts {
    position: absolute; left: 312px; top: 146px; list-style: none;
    font-family: "Work Sans", sans-serif; font-size: 17px; color: var(--ink); letter-spacing: 0.5px;
  }
  .contacts__item { display: flex; align-items: center; gap: 10px; height: 23px; }
  .contacts__icon { width: 14px; height: 14px; flex: none; fill: var(--accent); }
  .location {
    position: absolute; left: 56px; bottom: 32px;
    font-family: "Work Sans", sans-serif; font-size: 19px; color: var(--ink); letter-spacing: 0.5px;
  }
  .location__label { color: var(--accent); }
</style>
</head>
<body>
<main class="canvas">
  <section class="card card--front" aria-label="Card front">
    <div class="brand">
      <div class="brand__name">Valmira</div>
      <div class="brand__tagline">Integrative Holistic Medicine</div>
    </div>
    <p class="website">www.<span class="website__domain">valmirahealth</span>.example</p>
    <div class="card__stripe"></div>
  </section>

  <section class="card card--back" aria-label="Card back">
    <div class="identity">
      <h1 class="identity__name">Tobias Wrenfeld</h1>
      <p class="identity__credentials">DOE, CPT, LMT</p>
    </div>
    <div class="divider"></div>
    <ul class="contacts">
      <li class="contacts__item">
        <svg class="contacts__icon" viewBox="0 0 24 24"><path d="M6.6 10.8a15.1 15.1 0 0 0 6.6 6.6l2.2-2.2a1 1 0 0 1 1-.25 11.4 11.4 0 0 0 3.6.57 1 1 0 0 1 1 1V20a1 1 0 0 1-1 1A17 17 0 0 1 3 4a1 1 0 0 1 1-1h3.5a1 1 0 0 1 1 1c0 1.25.2 2.45.57 3.57a1 1 0 0 1-.25 1z"/></svg>
        512 555 0148
      </li>
      <li class="contacts__item">
        <svg class="contacts__icon" viewBox="0 0 24 24"><path d="M7 1h10a2 2 0 0 1 2 2v18a2 2 0 0 1-2 2H7a2 2 0 0 1-2-2V3a2 2 0 0 1 2-2zm0 3v14h10V4z"/></svg>
        818 555 0192
      </li>
      <li class="contacts__item">
        <svg class="contacts__icon" viewBox="0 0 24 24"><path d="M2 5h20v14H2z M2 5l10 8 10-8" fill="var(--accent)"/><path d="M3 6l9 7 9-7" stroke="#262626" stroke-width="1.5" fill="none"/></svg>
        info@ValmiraHealth.example
      </li>
      <li class="contacts__item">
        <svg class="contacts__icon" viewBox="0 0 24 24"><path d="M2 5h20v14H2z"/><path d="M3 6l9 7 9-7" stroke="#262626" stroke-width="1.5" fill="none"/></svg>
        t.wrenfeld@ValmiraHealth.example
      </li>
    </ul>
    <p class="location"><span class="location__label">Location:</span> 4100 East Marrow Drive&nbsp;&nbsp;Austin, TX 78119</p>
    <div class="card__stripe"></div>
  </section>
</main>
</body>
</html>
```